Business card design for my company.
I would like the card's background colour to be black. You can also see our web site to get an idea of our brand. https://www.tmwhomecrafting.com.au/
- Name
- Email

```html
<!DOCTYPE html>
<html lang="en">
<head>
<meta charset="utf-8">
<title>TMW Home Crafting – Business Card</title>
<link href="https://fonts.googleapis.com/css2?family=Montserrat:wght@400;500;700;800&display=swap" rel="stylesheet">
<style>
  :root {
    --stage: #3a3a3a;
    --card: #212121;
    --card-front: #232323;
    --front-mark: #1a1a1a;
    --green: #17994a;
    --white: #f2f2f2;
    --muted: #e6e6e6;
  }
  * { margin: 0; padding: 0; box-sizing: border-box; }
  html, body { width: 1200px; height: 875px; overflow: hidden; }
  body {
    background: var(--stage);
    font-family: "Montserrat", sans-serif;
    position: relative;
  }
  .card {
    position: absolute;
    width: 540px;
    height: 310px;
    border-radius: 22px;
    overflow: hidden;
    box-shadow: 0 18px 40px rgba(0,0,0,.45);
  }
  .card--front {
    left: 90px; top: 90px;
    background: var(--card-front);
    display: flex; align-items: center; justify-content: center;
  }
  .front-name {
    color: var(--front-mark);
    font-weight: 800;
    font-size: 40px;
    letter-spacing: 3px;
    text-transform: uppercase;
    text-align: center;
    line-height: 1.1;
  }
  .card--back {
    left: 570px; top: 475px;
    background: var(--card);
  }
  .back-band {
    position: absolute; left: 0; right: 0; bottom: 0;
    height: 16px; background: var(--green);
  }
  .back-brand {
    position: absolute; left: 40px; top: 108px;
    width: 200px;
    display: flex; align-items: center; gap: 10px;
  }
  .brand-square { width: 14px; height: 14px; background: var(--green); flex: none; }
  .brand-name {
    color: var(--white);
    font-weight: 800; font-size: 24px; line-height: 1.1;
    letter-spacing: 1.5px; text-transform: uppercase;
  }
  .back-divider {
    position: absolute; left: 262px; top: 60px;
    width: 1px; height: 170px; background: var(--green);
  }
  .back-details { position: absolute; left: 290px; top: 62px; right: 20px; }
  .person-name {
    color: var(--green); font-weight: 800; font-size: 24px;
    letter-spacing: 1px; text-transform: uppercase; line-height: 1.1;
  }
  .person-role { color: var(--muted); font-size: 14px; margin-top: 4px; }
  .contact-list { list-style: none; margin-top: 26px; }
  .contact-list li {
    color: var(--muted); font-size: 12.5px;
    display: flex; align-items: center; gap: 8px; margin-bottom: 9px;
  }
  .contact-icon { width: 12px; height: 12px; flex: none; }
</style>
</head>
<body>
  <section class="card card--front" aria-label="Card front">
    <p class="front-name">TMW<br>Home Crafting</p>
  </section>

  <section class="card card--back" aria-label="Card back">
    <div class="back-brand">
      <span class="brand-square"></span>
      <span class="brand-name">TMW Home Crafting</span>
    </div>
    <div class="back-divider"></div>
    <div class="back-details">
      <h1 class="person-name">Dorian Walsh</h1>
      <p class="person-role">CEO/Founder</p>
      <ul class="contact-list">
        <li>
          <svg class="contact-icon" viewBox="0 0 12 12"><path d="M2.5 1 L4.5 1 L5 3.5 L3.8 4.5 Q4.8 6.9 7.5 8.2 L8.5 7 L11 7.5 L11 9.5 Q10.5 11 9 11 Q1 10 1 3 Q1 1.5 2.5 1Z" fill="#17994a"/></svg>
          555-214-7390
        </li>
        <li>
          <svg class="contact-icon" viewBox="0 0 12 12"><rect x="0.5" y="2" width="11" height="8" fill="#17994a"/><path d="M0.5 2 L6 6.5 L11.5 2" stroke="#212121" stroke-width="1" fill="none"/></svg>
          info@tmwhomecrafting.com.au
        </li>
        <li>
          <svg class="contact-icon" viewBox="0 0 12 12"><circle cx="6" cy="6" r="5.2" fill="none" stroke="#17994a" stroke-width="1.2"/><ellipse cx="6" cy="6" rx="2.2" ry="5.2" fill="none" stroke="#17994a" stroke-width="1"/><line x1="0.8" y1="6" x2="11.2" y2="6" stroke="#17994a" stroke-width="1"/></svg>
          www.tmwhomecrafting.com.au
        </li>
      </ul>
    </div>
    <div class="back-band"></div>
  </section>
</body>
</html>
```